QRV Advisors needs a web site

We need a web site for www.qrvadvisors-example.com. QRV is a mergers and acquisition consulting company that focuses our buyer and seller services on logistics companies. We help put companies together, and help with legal and financial due diligence. We want the web site to express our service and show the logistics components. We want personalized images versus pictures of trucks and airplanes.

Our new logo uses Burgandy and grey colors. Image attached. We are not in to bold, big letters...classy, artistic, low key preferred. Confidentiality, experience, professional are what we want to express on the site.

All we expect for the first part of this project is a home page, and one subpage.  We are budgeting other funds for the technical aspects of the web site

Reason: All that I'm seeing so far is trucks, forklifts and planes. We are a legal mergers and acquisitions firm that focus on logistics. I like some of the images to say logistics, but really want it say legal, financial, and putting companies together. Will pay extra for the sub page if someone can impress us with a home page.

Reason: Swamped with another project at the moment...will work on this over the weekend and provide designer feedback and select final design by Tuesday

```html
<!DOCTYPE html>
<html lang="en">
<head>
<meta charset="utf-8">
<title>QRV Advisors – Home</title>
<link href="https://fonts.googleapis.com/css2?family=Ubuntu:wght@400;500;700&family=Rajdhani:wght@500;600&display=swap" rel="stylesheet">
<style>
:root{
  --burgundy:#a8063a;
  --grey-dark:#55565a;
  --grey-text:#555;
  --grey-mid:#888;
  --page:#f1f1f1;
  --footer:#2d2d2d;
  --white:#fff;
}
*{box-sizing:border-box;margin:0;padding:0}
html,body{width:1028px;height:1200px;overflow:hidden}
body{position:relative;background:var(--page);font-family:"Ubuntu",sans-serif;color:var(--grey-text)}
.abs{position:absolute}

/* header */
.topline{left:0;top:0;width:1028px;height:6px;background:#6d6d6d}
.header{left:0;top:6px;width:1028px;height:118px;background:linear-gradient(#f9f9f9,#e2e2e2)}
.brand{left:120px;top:48px;display:flex;align-items:center;gap:10px}
.brand-mark{font:500 36px/1 "Ubuntu",sans-serif;color:var(--grey-dark);letter-spacing:2px}
.brand-sep{width:1px;height:42px;background:var(--grey-mid)}
.brand-name{font:500 15px/1.05 "Ubuntu",sans-serif;color:var(--grey-dark);letter-spacing:.5px}
.social-top{left:648px;top:24px;display:flex;gap:10px}
.social-top span{width:28px;height:28px;border-radius:50%;background:radial-gradient(#555,#222)}
.call{left:776px;top:22px;display:flex;gap:8px;align-items:center}
.call-label{font-size:11px;color:#555}
.call-num{font-size:16px;color:#444}
.nav{left:378px;top:75px;display:flex;gap:12px}
.nav a{display:block;border-top:1px solid #bbb;border-bottom:1px solid #bbb;padding:7px 0;font-size:10px;color:#555;text-decoration:none;text-align:center}
.nav a.active{font-weight:700;color:#333;position:relative}
.nav a.active::before{content:"";position:absolute;left:50%;top:-1px;margin-left:-4px;border:4px solid transparent;border-top-color:#333}

/* hero */
.hero{left:0;top:124px;width:1028px;height:376px;background:radial-gradient(circle at 570px 170px,#f4e34a 0,#b9a419 55px,#2b2b2b 130px,#141414 420px)}
.arrow{top:308px}
.caption{left:118px;top:422px;width:792px;height:78px;background:rgba(240,240,240,.92);text-align:center;padding-top:12px;font:700 25px/33px "Ubuntu",sans-serif;color:#5b5b5b}

/* services */
.services-title{left:0;top:516px;width:1028px;text-align:center;font:600 28px/1 "Rajdhani",sans-serif;color:var(--burgundy)}
.rule{top:530px;height:1px;background:linear-gradient(90deg,transparent,#bbb,transparent)}
.card{top:563px;width:237px;height:147px;background:var(--white);box-shadow:0 1px 4px rgba(0,0,0,.18)}
.card-head{height:91px;position:relative;color:var(--white);font:500 22px/23px "Rajdhani",sans-serif;padding:40px 0 0 11px}
.card-head svg{position:absolute;right:8px;bottom:0}
.card p{font-size:10.5px;line-height:14.5px;padding:4px 7px 0 10px;color:#555}
.band{left:0;top:722px;width:1028px;height:16px;background:radial-gradient(ellipse at center,rgba(0,0,0,.12),transparent 70%)}

/* panels */
.panel{top:760px;width:252px;height:230px;background:var(--white);border-radius:4px;box-shadow:0 4px 5px -3px rgba(60,90,120,.35)}
.panel-head{position:absolute;left:-4px;right:-4px;top:12px;height:31px;background:var(--grey-dark);color:var(--white);font-size:17px;display:flex;align-items:center;gap:10px;padding-left:12px;letter-spacing:.5px}
.photo{left:12px;top:59px;width:227px;height:88px;background:linear-gradient(90deg,#37414f,#bdc6d0 50%,#2d3644)}
.about-text{left:18px;top:152px;width:220px;font-size:9.5px;line-height:12px;color:#444;letter-spacing:.3px}
.more{right:10px;bottom:16px;font-size:9.5px;font-weight:700;color:#555}
.news{left:12px;width:232px;display:flex;gap:10px}
.date{width:31px;text-align:center;font-size:10px;font-weight:700;flex:none}
.date b{display:block;background:var(--burgundy);color:var(--white);padding:1px 0}
.date i{display:block;font-style:normal;background:#f4f4f4;color:#444;padding:2px 0;border:1px solid #ddd}
.news p{font-size:9.5px;line-height:12px;color:#444}
.news p strong{color:#222}
.field{left:12px;width:225px;height:20px;border:1px solid #bbb;border-radius:2px;font-size:10px;color:#666;padding:3px 8px}
.submit{left:14px;top:202px;width:56px;height:19px;background:var(--burgundy);color:var(--white);font-size:12px;font-weight:700;text-align:center;line-height:19px}

/* footer */
.footer{left:0;top:1018px;width:1028px;height:182px;background:var(--footer);border-top:4px solid var(--burgundy)}
.f-title{font-size:15px;color:#eee}
.f-links{left:118px;top:1066px;list-style:none;font-size:10px;line-height:14.3px;color:#ddd}
.f-links li::before{content:"›";margin-right:7px;color:#aaa}
.vsep{width:1px;height:110px;background:#555;top:1038px}
.map{left:288px;top:1068px;width:185px;height:80px;background:linear-gradient(135deg,#e6e4de,#d3d0c8)}
.f-contact{left:480px;font-size:10.5px;line-height:15px;color:#ddd;display:flex;gap:8px;align-items:flex-start}
.f-brand{left:730px;top:1040px;width:180px;text-align:center;font:500 62px/1 "Ubuntu",sans-serif;color:var(--white);letter-spacing:6px}
.f-social{left:764px;top:1117px;display:flex;gap:10px}
.f-social span{width:31px;height:31px;border-radius:6px}
.copy{left:0;top:1170px;width:1028px;text-align:center;font-size:13px;color:#ddd}
</style>
</head>
<body>
<div class="abs topline"></div>
<header class="abs header"></header>
<div class="abs brand">
  <span class="brand-mark">QRV</span><span class="brand-sep"></span>
  <span class="brand-name">QRV<br>ADVISORS</span>
</div>
<div class="abs social-top" aria-label="Social links"><span></span><span></span><span></span></div>
<div class="abs call">
  <svg width="28" height="28" viewBox="0 0 28 28"><circle cx="14" cy="14" r="12.5" fill="none" stroke="#a8063a" stroke-width="2"/><path d="M10 8c-2 2-1 6 3 10s7 4 8 2l-2-3-2 1c-1 0-4-3-4-4l1-2z" fill="#a8063a"/></svg>
  <div><div class="call-label">Call Us Today</div><div class="call-num">123 456 7890</div></div>
</div>
<nav class="abs nav">
  <a class="active" style="width:40px">HOME</a>
  <a style="width:65px">ABOUT US</a>
  <a style="width:84px">BUYER SERVICES</a>
  <a style="width:82px">SELLER SERVICES</a>
  <a style="width:81px">NEWS &amp; EVENTS</a>
  <a style="width:40px">FAQ's</a>
  <a style="width:64px">CONTACT</a>
</nav>

<div class="abs hero" role="img" aria-label="Hand holding a glowing light bulb among outlined bulbs on a dark suit"></div>
<svg class="abs arrow" style="left:80px" width="24" height="36" viewBox="0 0 24 36"><path d="M20 2L4 18l16 16" fill="none" stroke="#999" stroke-width="5"/></svg>
<svg class="abs arrow" style="left:924px" width="24" height="36" viewBox="0 0 24 36"><path d="M4 2l16 16L4 34" fill="none" stroke="#999" stroke-width="5"/></svg>
<div class="abs caption">QRV Services Are Offered By Industry Executives With Extensive<br>M&amp;A Experience</div>

<div class="abs rule" style="left:200px;width:222px"></div>
<div class="abs rule" style="left:616px;width:224px"></div>
<h2 class="abs services-title">Our Services</h2>

<section class="abs card" style="left:119px">
  <div class="card-head" style="background:var(--burgundy)">Business<br>Planning
    <svg width="60" height="62" viewBox="0 0 60 62"><rect x="6" y="4" width="44" height="58" fill="none" stroke="#fff" stroke-width="4"/><path d="M14 16h28M14 25h28M14 34h20" stroke="#fff" stroke-width="4"/><path d="M28 46l8 8 20-20" fill="none" stroke="#fff" stroke-width="5"/></svg>
  </div>
  <p>Lorem ipsum dolor sit amet, consectetuer eadi pis elit, sed diam nonummy nibh euismod tinc idunt ut laoreeio dolore magna aliquam erate</p>
</section>
<section class="abs card" style="left:394px">
  <div class="card-head" style="background:var(--grey-dark)">Mergers &amp;<br>Acquisition
    <svg width="70" height="50" viewBox="0 0 70 50"><path d="M2 20l18-12 14 6 14-6 20 12-8 14-20 10-18-8z" fill="#fff"/><path d="M22 22l10 8M30 18l12 10" stroke="#55565a" stroke-width="3"/></svg>
  </div>
  <p>Lorem ipsum dolor sit amet, consectetuer eadi pis elit, sed diam nonummy nibh euismod tinc idunt ut laoreeio dolore magna aliquam erate</p>
</section>
<section class="abs card" style="left:670px">
  <div class="card-head" style="background:var(--grey-dark)">Advisory<br>Services
    <svg width="60" height="50" viewBox="0 0 60 50"><rect x="24" y="2" width="32" height="22" rx="3" fill="none" stroke="#fff" stroke-width="3"/><path d="M30 10h20M30 16h14" stroke="#fff" stroke-width="2"/><circle cx="18" cy="22" r="7" fill="#fff"/><path d="M2 50c0-12 6-18 16-18s16 6 16 18z" fill="#fff"/></svg>
  </div>
  <p>Lorem ipsum dolor sit amet, consectetuer eadi pis elit, sed diam nonummy nibh euismod tinc idunt ut laoreeio dolore magna aliquam erate</p>
</section>
<div class="abs band"></div>

<section class="abs panel" style="left:122px">
  <div class="panel-head"><svg width="20" height="16" viewBox="0 0 20 16" fill="#fff"><circle cx="5" cy="5" r="3"/><circle cx="15" cy="5" r="3"/><circle cx="10" cy="7" r="3.5"/><path d="M3 16c0-5 3-6 7-6s7 1 7 6z"/></svg>ABOUT QRV</div>
  <div class="abs photo" role="img" aria-label="Business team in conversation at an office"></div>
  <p class="abs about-text">QRV assists business owners within the logistics industry to implement growth and exit strategies. We offer business planning and merger and acquisition (M&amp;A) advisory services.</p>
  <span class="abs more">Read More »</span>
</section>

<section class="abs panel" style="left:394px">
  <div class="panel-head"><svg width="16" height="16" viewBox="0 0 16 16"><rect x="1" y="2" width="14" height="13" fill="none" stroke="#fff" stroke-width="1.5"/><path d="M1 6h14M5 9h2M9 9h2M5 12h2M9 12h2" stroke="#fff" stroke-width="1.5"/></svg>NEWS &amp; EVENTS</div>
  <div class="abs news" style="top:59px"><div class="date"><b>Apr</b><i>02</i></div><p><strong>Lorem ipsum dolor sit amet, consectetue</strong><br>eadi pis elit, sed diam nonummy nibherini euismod tinc idunt ut laoreeio.</p></div>
  <div class="abs news" style="top:107px"><div class="date"><b>Apr</b><i>03</i></div><p><strong>Lorem ipsum dolor sit amet, consectetue</strong><br>eadi pis elit, sed diam nonummy nibherini euismod tinc idunt ut laoreeio.</p></div>
  <div class="abs news" style="top:155px"><div class="date"><b>Apr</b><i>04</i></div><p><strong>Lorem ipsum dolor sit amet, consectetue</strong><br>eadi pis elit, sed diam nonummy nibherini euismod tinc idunt ut laoreeio.</p></div>
  <span class="abs more">Read More »</span>
</section>

<section class="abs panel" style="left:664px">
  <div class="panel-head"><svg width="16" height="16" viewBox="0 0 16 16"><path d="M2 1h9v5M2 1v14h6" fill="none" stroke="#fff" stroke-width="1.5"/><path d="M8 14l1-3 6-6 2 2-6 6z" fill="#fff"/></svg>QUICK CONTACT</div>
  <div class="abs field" style="top:59px">Name</div>
  <div class="abs field" style="top:87px">Email</div>
  <div class="abs field" style="top:116px">Phone</div>
  <div class="abs field" style="top:144px;height:52px">Message</div>
  <div class="abs submit">Submit</div>
</section>

<footer class="abs footer"></footer>
<div class="abs f-title" style="left:118px;top:1036px">Quick Links</div>
<div class="abs" style="left:118px;top:1059px;width:104px;border-top:1px dotted #666"></div>
<ul class="abs f-links"><li>Home</li><li>About Us</li><li>Consulting Services</li><li>News &amp; Events</li><li>FAQ's</li><li>Contact Us</li></ul>
<div class="abs vsep" style="left:255px"></div>
<div class="abs f-title" style="left:288px;top:1036px">Contact Us</div>
<div class="abs" style="left:288px;top:1059px;width:376px;border-top:1px dotted #666"></div>
<div class="abs map" role="img" aria-label="Street map showing the office location"></div>
<div class="abs f-contact" style="top:1068px"><svg width="16" height="16" viewBox="0 0 16 16"><path d="M1 8L8 2l7 6M3 7v8h4v-4h2v4h4V7" fill="none" stroke="#fff" stroke-width="1.6"/></svg><span>Lorem ipsum dolor sit amet, conse<br>adipiscing elit, sed diam nonummy.</span></div>
<div class="abs f-contact" style="top:1105px"><svg width="16" height="16" viewBox="0 0 16 16"><circle cx="8" cy="8" r="7" fill="none" stroke="#fff" stroke-width="1.4"/><path d="M6 4c-1 1-1 4 2 7l2 0 0-2-1-1-1 1c-1-1-2-2-2-3l1-1z" fill="#fff"/></svg><span>123.456.7890</span></div>
<div class="abs f-contact" style="top:1132px"><svg width="16" height="16" viewBox="0 0 16 16"><circle cx="8" cy="8" r="3" fill="none" stroke="#fff" stroke-width="1.6"/><path d="M11 5v4c0 2 3 2 3-1A6 6 0 1 0 11 13" fill="none" stroke="#fff" stroke-width="1.6"/></svg><span>info@qrvadvisors-example.com</span></div>
<div class="abs vsep" style="left:700px"></div>
<div class="abs f-brand">QRV</div>
<div class="abs f-social" aria-label="Social links"><span style="background:#3a5a98"></span><span style="background:#2ca7e0"></span><span style="background:#f07a1f"></span></div>
<div class="abs copy">© 2014 qrvadvisors-example.com.&nbsp; All Rights Reserved .</div>
</body>
</html>
```